Birchline Septic Solutions

Would like to see some single sided ones but would also like to see some double sided with one sided only being the logo. Owners name is Colin Vandro. Phone number is 555-214-0387
Services are pumping, inspections, installs, and repairs

Contact Information for Business Card

555-241-0387 Colin Vandro Alder Falls, OH

```html
<!DOCTYPE html>
<html lang="en">
<head>
<meta charset="UTF-8">
<title>Birchline Septic Solutions — Business Card</title>
<link rel="stylesheet" href="https://fonts.googleapis.com/css2?family=Montserrat:wght@400;500;700;800&display=swap">
<style>
  :root {
    --backdrop: #2a2a2b;
    --card: #1e1f21;
    --card-back: #18191a;
    --pattern-light: #2c2d2f;
    --pattern-dark: #121213;
    --white: #ffffff;
    --teal: #2ec4b6;
    --rule: #5a5b5e;
  }
  * { box-sizing: border-box; margin: 0; padding: 0; }
  html, body {
    width: 1200px;
    height: 1108px;
    overflow: hidden;
    background: var(--backdrop);
    font-family: "Montserrat", sans-serif;
  }
  .stage {
    position: relative;
    width: 1200px;
    height: 1108px;
    display: flex;
    justify-content: center;
    align-items: center;
    gap: 80px;
  }
  .card {
    width: 400px;
    height: 700px;
    border-radius: 26px;
    position: relative;
    overflow: hidden;
    box-shadow: 0 24px 50px rgba(0,0,0,0.45);
  }
  .card-front {
    background: var(--card);
    color: var(--white);
    display: flex;
    flex-direction: column;
    align-items: center;
    padding-top: 110px;
    text-align: center;
  }
  .brand-name {
    display: flex;
    align-items: center;
    gap: 12px;
    font-weight: 800;
    font-size: 46px;
    letter-spacing: 1px;
    line-height: 1;
  }
  .brand-dot {
    width: 14px;
    height: 14px;
    border-radius: 50%;
    background: var(--teal);
  }
  .brand-tagline {
    margin-top: 16px;
    font-weight: 500;
    font-size: 15px;
    letter-spacing: 6px;
  }
  .owner-name {
    margin-top: 70px;
    font-weight: 800;
    font-size: 26px;
    letter-spacing: 0.5px;
  }
  .contact-row {
    margin-top: 34px;
    display: flex;
    flex-direction: column;
    align-items: center;
  }
  .contact-row + .contact-row { margin-top: 22px; }
  .icon-divider {
    display: flex;
    align-items: center;
    gap: 6px;
  }
  .icon-divider .rule {
    width: 70px;
    height: 1px;
    background: var(--rule);
  }
  .icon-ring {
    width: 44px;
    height: 44px;
    border: 2px solid var(--teal);
    border-radius: 50%;
    display: flex;
    align-items: center;
    justify-content: center;
  }
  .contact-text {
    margin-top: 10px;
    font-weight: 500;
    font-size: 21px;
    letter-spacing: 0.5px;
  }
  .section-rule {
    margin-top: 26px;
    width: 210px;
    height: 1px;
    background: var(--rule);
  }
  .services {
    margin-top: 16px;
    font-weight: 500;
    font-size: 17px;
    letter-spacing: 1px;
    line-height: 1.45;
  }
  .services .dot {
    display: inline-block;
    width: 9px;
    height: 9px;
    border-radius: 50%;
    background: var(--teal);
    margin: 0 8px;
    vertical-align: middle;
  }
  .card-back {
    background: var(--card-back);
  }
  .back-pattern {
    position: absolute;
    inset: 0;
    background: linear-gradient(160deg, var(--pattern-light) 0%, var(--card-back) 55%, var(--pattern-dark) 100%);
  }
  .back-mark {
    position: absolute;
    left: 50%;
    top: 66%;
    transform: translateX(-40%);
    font-weight: 800;
    font-size: 28px;
    color: var(--white);
    letter-spacing: 0.5px;
  }
</style>
</head>
<body>
  <main class="stage">
    <section class="card card-front" aria-label="Business card front">
      <div class="brand-name"><span class="brand-dot"></span>BIRCHLINE</div>
      <div class="brand-tagline">SEPTIC SOLUTIONS</div>

      <h1 class="owner-name">COLIN VANDRO</h1>

      <div class="contact-row">
        <div class="icon-divider">
          <span class="rule"></span>
          <span class="icon-ring">
            <svg width="20" height="20" viewBox="0 0 24 24" aria-hidden="true">
              <path d="M6.6 10.8a15.1 15.1 0 0 0 6.6 6.6l2.2-2.2a1 1 0 0 1 1-.25 11.4 11.4 0 0 0 3.6.57 1 1 0 0 1 1 1V20a1 1 0 0 1-1 1A17 17 0 0 1 3 4a1 1 0 0 1 1-1h3.5a1 1 0 0 1 1 1c0 1.25.2 2.45.57 3.57a1 1 0 0 1-.25 1z" fill="var(--teal)"/>
            </svg>
          </span>
          <span class="rule"></span>
        </div>
        <div class="contact-text">555-214-0387</div>
      </div>

      <div class="contact-row">
        <div class="icon-divider">
          <span class="rule"></span>
          <span class="icon-ring">
            <svg width="20" height="20" viewBox="0 0 24 24" aria-hidden="true">
              <path d="M12 2a7 7 0 0 0-7 7c0 5.25 7 13 7 13s7-7.75 7-13a7 7 0 0 0-7-7zm0 9.5A2.5 2.5 0 1 1 12 6.5a2.5 2.5 0 0 1 0 5z" fill="var(--teal)"/>
            </svg>
          </span>
          <span class="rule"></span>
        </div>
        <div class="contact-text">Alder Falls, OH</div>
      </div>

      <div class="section-rule"></div>
      <p class="services">
        PUMPING<span class="dot"></span>INSPECTIONS<br>
        INSTALLS<span class="dot"></span>REPAIRS
      </p>
    </section>

    <section class="card card-back" aria-label="Business card back">
      <div class="back-pattern" role="img" aria-label="Repeating tone-on-tone brand pattern in glossy black"></div>
      <div class="back-mark">BIRCHLINE</div>
    </section>
  </main>
</body>
</html>
```